We need a new business card that reflects who we are. Professional, classy, modern, and service ori

We need a business card design for a window coverings design company in Kansas City called Bright Lane Interiors. We offer professional, modern, and high quality window covering products. We are looking to portray an image of a big, national franchise. We are a 5 location (with showrooms) business with 10 professional designers and 4 professional installers. These cards will be used with Thank you cards, given to realtors, and asked for referrals with.

Target Market(s)

Kansas City

Industry/Entity Type

Business

Contact Information for Business Card

We would like our card to look clean and simple on the front, featuring our logo and Marlow Fenwick's. Our designers' phone numbers and emails should be displayed as well as their title.

Font styles to use
Sans Serif

Colors

Designer to choose colors to be used in the design.

Requirements
Must have
• Front - Logos, name, phone number, email address
• Back - Showroom locations, social media? Appt date/time?
Nice to have
• I would like a clean and modern look (not contemporary. I like a white background, but I am open to ideas. Looking for a "National chain" look for a small business.
Should not have
• Too much busyness.

```html
<!DOCTYPE html>
<html lang="en">
<head>
<meta charset="utf-8">
<title>Bright Lane Interiors – Business Card</title>
<link href="https://fonts.googleapis.com/css2?family=Roboto:wght@400;500;700&family=Roboto+Condensed:wght@500;700&display=swap" rel="stylesheet">
<style>
  :root {
    --backdrop: #2b2b2b;
    --card: #f4f4f4;
    --red: #c4383e;
    --grey: #939598;
    --ink: #111111;
    --text: #4a4a4a;
    --list: #585858;
    --rule: #8a8a8a;
  }
  * { margin: 0; padding: 0; box-sizing: border-box; }
  html, body { width: 1200px; height: 960px; overflow: hidden; }
  body {
    background: var(--backdrop);
    position: relative;
    font-family: "Roboto", Arial, sans-serif;
    color: var(--text);
  }
  .card {
    position: absolute;
    width: 600px;
    height: 343px;
    background: var(--card);
    box-shadow: 0 3px 10px rgba(0,0,0,.45);
  }
  .card--front { left: 314px; top: 113px; }
  .card--back  { left: 311px; top: 472px; }

  .brand { position: absolute; }
  .brand__mark { display: flex; align-items: center; gap: 10px; }
  .brand__square { width: 26px; height: 26px; background: var(--red); }
  .brand__name {
    font-family: "Roboto", Arial, sans-serif;
    font-weight: 500;
    font-size: 24px;
    color: var(--ink);
    letter-spacing: .2px;
    white-space: nowrap;
  }
  .brand__tagline {
    margin-top: 8px;
    font-size: 11.5px;
    color: var(--ink);
    white-space: nowrap;
  }
  .card--front .brand { left: 40px; top: 122px; }
  .card--back .brand  { left: 52px; top: 125px; }

  .person { position: absolute; right: 41px; top: 205px; text-align: right; }
  .person__name {
    font-family: "Roboto Condensed", Arial, sans-serif;
    font-weight: 500; font-size: 23px; color: var(--red); line-height: 1;
  }
  .person__title {
    margin-top: 5px;
    font-size: 14px; font-weight: 500; color: var(--ink); letter-spacing: .3px;
  }
  .rule {
    position: absolute; left: 42px; top: 243px; width: 428px; height: 1px; background: var(--rule);
  }
  .contact {
    position: absolute; left: 40px; top: 264px; font-size: 14.5px; line-height: 20px; color: var(--text);
  }
  .web-band {
    position: absolute; left: 285px; top: 282px; width: 315px; height: 22px; background: var(--grey);
  }
  .web-band__label {
    position: absolute; left: 28px; top: 0; width: 257px; height: 22px;
    background: var(--red); color: #fff;
    font-size: 14px; letter-spacing: 1.2px; line-height: 22px; text-align: center;
  }

  .showrooms {
    position: absolute; right: 53px; top: 43px; text-align: right;
    font-size: 14px; font-weight: 500; line-height: 18px; color: var(--list);
  }
  .showrooms__heading { color: var(--red); }
  .partner {
    position: absolute; right: 53px; top: 157px;
    display: flex; align-items: center; gap: 5px;
    font-size: 13px; font-weight: 700; color: #56606a;
  }
  .partner__dot { width: 14px; height: 14px; border-radius: 50%; background: #f08a24; }
  .social { position: absolute; right: 53px; top: 185px; display: flex; gap: 3px; }
  .social__dot { width: 17px; height: 17px; border-radius: 50%; background: var(--red); }

  .appointment {
    position: absolute; left: 52px; width: 498px; display: flex; align-items: baseline;
    color: var(--red); font-size: 16px;
  }
  .appointment--name { top: 237px; }
  .appointment--when { top: 278px; }
  .appointment__fill {
    flex: 1; border-bottom: 1px dotted #555; margin: 0 4px; height: 12px;
  }
  .appointment__fill--date { flex: 0 0 214px; margin-right: 2px; }
  .appointment__suffix { font-size: 12px; }
</style>
</head>
<body>

  <section class="card card--front">
    <div class="brand">
      <div class="brand__mark">
        <span class="brand__square"></span>
        <span class="brand__name">Bright Lane Interiors</span>
      </div>
      <div class="brand__tagline">Blinds, Shades, Shutters, Draperies &amp; Decor</div>
    </div>

    <div class="person">
      <div class="person__name">DANIEL REYES</div>
      <div class="person__title">DESIGNER</div>
    </div>
    <div class="rule"></div>

    <div class="contact">
      <div class="contact__phone">913.555.0148</div>
      <div class="contact__email">info@brightlaneinteriors.com</div>
    </div>

    <div class="web-band">
      <div class="web-band__label">www.brightlaneinteriors.com</div>
    </div>
  </section>

  <section class="card card--back">
    <div class="brand">
      <div class="brand__mark">
        <span class="brand__square"></span>
        <span class="brand__name">Bright Lane Interiors</span>
      </div>
      <div class="brand__tagline">Blinds, Shades, Shutters, Draperies &amp; Decor</div>
    </div>

    <div class="showrooms">
      <div class="showrooms__heading">SHOWROOM LOCATIONS</div>
      <div>MAPLE HEIGHTS</div>
      <div>CEDAR CROSSING</div>
      <div>BROOKFIELD</div>
      <div>NORTHGATE</div>
      <div>RIVERBEND</div>
    </div>

    <div class="partner">
      <span class="partner__name">Marlow Fenwick</span>
      <span class="partner__dot"></span>
    </div>

    <div class="social" aria-label="Social media">
      <span class="social__dot"></span>
      <span class="social__dot"></span>
      <span class="social__dot"></span>
      <span class="social__dot"></span>
    </div>

    <div class="appointment appointment--name">
      <span>Name :</span><span class="appointment__fill"></span>
    </div>
    <div class="appointment appointment--when">
      <span>Date :</span><span class="appointment__fill appointment__fill--date"></span>
      <span>Time :</span><span class="appointment__fill"></span>
      <span class="appointment__suffix">AM/PM</span>
    </div>
  </section>

</body>
</html>
```